Harbor Ledger Funds Bus card and Logo

I need a logo design and Bus card design. The fund focuses on evaluating and investing in minerals (sub-surface rights) and real estate.

Harbor ledger refers to a book of knowledge that each plebe gets when entering the Kelmont Marine Academy (my alma mater)

Target Market(s)

Investors and financial advisors

Contact Information for Business Card

Simple - perhaps a logo with a theme on book of knowledge

Logo Text

Ex Scientia Imperium

Font styles to use
Serif
Sans Serif

Colors

Designer to choose colors to be used in the design.

Requirements
Must have
• memorable logo that is relatively simple

```html
<!DOCTYPE html>
<html lang="en">
<head>
<meta charset="utf-8">
<title>Harbor Ledger Funds – Business Card</title>
<link rel="stylesheet" href="https://fonts.googleapis.com/css2?family=Arimo:wght@400;700&display=swap">
<style>
  :root {
    --navy: #1e3f8f;
    --navy-deep: #17327a;
    --lime: #a9cf3a;
    --paper: #f4f5f6;
    --white: #ffffff;
    --stage: #e6e8eb;
  }
  * { margin: 0; padding: 0; box-sizing: border-box; }
  html, body { width: 1200px; height: 780px; overflow: hidden; }
  body {
    background: var(--stage);
    font-family: "Arimo", Arial, sans-serif;
    position: relative;
  }
  .card {
    position: absolute;
    width: 540px;
    height: 310px;
    border-radius: 14px;
    overflow: hidden;
    background: var(--paper);
    box-shadow: 0 10px 28px rgba(20, 30, 60, 0.18);
  }
  .card-front { left: 45px; top: 235px; }
  .card-back  { left: 615px; top: 235px; }
  .card-art { position: absolute; inset: 0; }

  .brand-name {
    position: absolute;
    color: var(--navy);
    font-weight: 700;
    line-height: 1.02;
    letter-spacing: -0.5px;
  }
  .card-front .brand-name { left: 44px; top: 58px; font-size: 38px; width: 260px; }
  .card-back .brand-name { left: 0; right: 0; top: 58px; font-size: 40px; text-align: center; }
  .brand-suffix { display: block; font-size: 16px; letter-spacing: 2px; margin-top: 8px; }

  .contact-block {
    position: absolute;
    right: 22px;
    top: 214px;
    display: flex;
    align-items: center;
    gap: 12px;
    white-space: nowrap;
  }
  .person-name { color: var(--lime); font-weight: 700; font-size: 20px; }
  .person-role { color: var(--lime); font-size: 13px; margin-top: 2px; text-align: right; }
  .divider { width: 2px; height: 40px; background: var(--lime); }
  .contact-lines { color: var(--white); font-size: 12px; line-height: 1.7; }
  .contact-lines li { list-style: none; display: flex; align-items: center; gap: 7px; }
  .contact-lines svg { width: 10px; height: 10px; flex: none; }

  .address-strip {
    position: absolute;
    left: 0; right: 0; bottom: 0;
    height: 34px;
    display: flex;
    align-items: center;
    justify-content: flex-end;
    padding-right: 26px;
    color: var(--white);
    font-size: 13px;
    letter-spacing: 0.8px;
    white-space: nowrap;
  }
  .web-address {
    position: absolute;
    left: 44px;
    bottom: 18px;
    color: var(--white);
    font-size: 14px;
    letter-spacing: 2.5px;
    white-space: nowrap;
  }
</style>
</head>
<body>

<section class="card card-front">
  <svg class="card-art" viewBox="0 0 540 310" aria-hidden="true">
    <path d="M0 256 C 170 240, 350 150, 405 0 L540 0 L540 276 L0 276 Z" fill="var(--navy)"/>
    <path d="M0 244 C 165 228, 340 140, 390 0" fill="none" stroke="var(--lime)" stroke-width="3"/>
    <rect x="0" y="276" width="540" height="34" fill="var(--lime)"/>
  </svg>
  <div class="brand-name">Harbor Ledger Funds</div>
  <div class="contact-block">
    <div>
      <div class="person-name">Ellis Warren</div>
      <div class="person-role">Founder</div>
    </div>
    <div class="divider"></div>
    <ul class="contact-lines">
      <li><svg viewBox="0 0 10 10"><rect x="1" y="1" width="8" height="8" fill="none" stroke="#fff" stroke-width="1.4"/></svg>(555) 014-2290</li>
      <li><svg viewBox="0 0 10 10"><rect x="0.5" y="1.5" width="9" height="7" fill="#fff"/><path d="M0.5 1.5 L5 5.5 L9.5 1.5" fill="none" stroke="var(--navy)" stroke-width="1"/></svg>info@harborledger.com</li>
    </ul>
  </div>
  <div class="address-strip">PO BOX 48, Quay Road, Dock Lane, Kelmont</div>
</section>

<section class="card card-back">
  <svg class="card-art" viewBox="0 0 540 310" aria-hidden="true">
    <path d="M0 178 C 120 255, 330 288, 540 292 L540 310 L0 310 Z" fill="var(--navy)"/>
    <path d="M0 162 C 120 240, 330 274, 540 279" fill="none" stroke="var(--lime)" stroke-width="3"/>
  </svg>
  <div class="brand-name">Harbor Ledger Funds<span class="brand-suffix">LLC</span></div>
  <div class="web-address">www.harborledgerfunds.com</div>
</section>

</body>
</html>
```